Envelope Design - Winner can do follow-up business

- Varnoko.com is a Swiss-based online store selling business shirts and accessories for business men
- Please visit the webpage to make yourself familiar with the company. Although the text is in German, with Plimbo translator you should be able to understand the main content.
- Our clients are mainly business men between 30 and 60 years old. Mostly with a high income working in the service industry (banking, insurance, lawyers, etc.). Sometimes there wives purchase the shirts for them ;-)
- The colors and the logo are given, as they are also used for the print materials (please see files in attachment)
- I am running several businesses and often need a talented web designer --> the winner gets substantial follow-up business
your task:
-for our company we need a new envelope design
-It should be simple and modern
-please use one of the logos in the followings.
-suprise me :)

```html
<!DOCTYPE html>
<html lang="en">
<head>
<meta charset="utf-8">
<title>Varnoko Envelope Set</title>
<link rel="stylesheet" href="https://fonts.googleapis.com/css2?family=Montserrat:wght@500&family=Roboto+Slab:wght@400&display=swap">
<style>
  :root {
    --bg: #ece9e4;
    --paper: #ffffff;
    --edge: #6b6b6b;
    --gold: #e8d86d;
    --gold-soft: #f3eab0;
    --red: #ee2e24;
    --ink: #1a1a1a;
  }
  * { margin: 0; padding: 0; box-sizing: border-box; }
  html, body { width: 1200px; height: 909px; overflow: hidden; background: var(--bg); }
  .canvas { position: relative; width: 1200px; height: 909px; }

  .envelope {
    position: absolute;
    background: var(--paper);
    border: 1px solid var(--edge);
    overflow: hidden;
  }
  .envelope-back  { left: 246px; top: 76px;  width: 926px; height: 436px; }
  .envelope-flap  { left: 159px; top: 238px; width: 927px; height: 437px; }
  .envelope-front { left: 31px;  top: 401px; width: 928px; height: 437px; }

  .flap-shape { position: absolute; left: 0; top: 0; display: block; }

  .wordmark {
    position: absolute;
    font-family: "Montserrat", sans-serif;
    font-weight: 500;
    letter-spacing: 3px;
    line-height: 1;
    white-space: nowrap;
  }
  .envelope-back .wordmark  { color: var(--red);  font-size: 44px; left: 463px; top: 47px; transform: translateX(-50%); }
  .envelope-flap .wordmark  { color: var(--gold); font-size: 44px; left: 464px; top: 47px; transform: translateX(-50%); }
  .envelope-front .wordmark { color: var(--gold); font-size: 44px; left: 17px; top: 88px; }

  .contact {
    position: absolute;
    font-family: "Roboto Slab", serif;
    font-size: 19px;
    color: var(--ink);
    line-height: 24px;
    display: flex;
    align-items: flex-start;
    gap: 12px;
  }
  .contact svg { flex: none; margin-top: 2px; }
  .contact-web { left: 52px; top: 140px; align-items: center; }
  .contact-address { left: 613px; top: 382px; z-index: 2; }
  .contact-address address { font-style: normal; }

  .footer-band {
    position: absolute;
    left: 0;
    right: 0;
    bottom: 0;
    height: 130px;
    background: linear-gradient(to bottom, var(--gold-soft) 0%, var(--gold) 55%, var(--gold) 100%);
  }
</style>
</head>
<body>
<main class="canvas">

  <section class="envelope envelope-back">
    <svg class="flap-shape" width="926" height="146" viewBox="0 0 926 146">
      <path fill="var(--gold)" d="M0,0 L926,0 C916,48 904,68 830,83 L520,140 Q490,146 463,146 Q436,146 406,140 L96,83 C22,68 10,48 0,0 Z"/>
    </svg>
    <div class="wordmark">VARNOKO</div>
  </section>

  <section class="envelope envelope-flap">
    <svg class="flap-shape" width="927" height="148" viewBox="0 0 927 148">
      <path fill="none" stroke="var(--edge)" stroke-width="1" d="M0,0 C10,48 22,68 96,83 L406,140 Q436,146 463,146 Q490,146 520,140 L830,83 C904,68 916,48 927,0"/>
    </svg>
    <div class="wordmark">VARNOKO</div>
  </section>

  <section class="envelope envelope-front">
    <div class="footer-band" role="img" aria-label="Decorative flowing red and gold wave band along the bottom of the envelope"></div>

    <div class="wordmark">VARNOKO</div>

    <div class="contact contact-web">
      <svg width="22" height="22" viewBox="0 0 22 22" fill="none" stroke="var(--red)" stroke-width="1.6">
        <circle cx="11" cy="11" r="9.5"/>
        <ellipse cx="11" cy="11" rx="4.2" ry="9.5"/>
        <line x1="1.5" y1="11" x2="20.5" y2="11"/>
        <path d="M3,6 H19 M3,16 H19"/>
      </svg>
      <span>www.varnoko.com</span>
    </div>

    <div class="contact contact-address">
      <svg width="18" height="24" viewBox="0 0 18 24">
        <path fill="var(--red)" d="M9,0 C4,0 0,4 0,9 C0,15 9,24 9,24 C9,24 18,15 18,9 C18,4 14,0 9,0 Z"/>
        <circle cx="9" cy="9" r="3.4" fill="var(--gold)"/>
      </svg>
      <address>Street Name, City Name<br>State Zipcode</address>
    </div>
  </section>

</main>
</body>
</html>
```